Home Page for a Swiss based start up company, trading Natural & Health food ingredients (B2B)

I would like to create a home page for my new start up company (Veltrana Swiss AG), the main field of activity is the trading and marketing of Natural and Health food ingredients towards the functional Food and Food supplements industry. (B2B).
Target Market : Functional Food and Food Supplement Manufacturers (B2B) based in Switzerland and Europe
The values I would like to convey are :
- sourcing of natural and health ingredients, (example : natural plant extracts, Omega 3, plant proteins, natural vitamins, vegan food ingredients...etc)
- Health & Nutritional Health
- Eco-friendly and Sustainability
- High Quality Standard in term of products and logistic services
- Trust and reliability
- Flexibility & speed to market
-Technical advice for the development of new products

The site will be translated in 3 languages (German, French, English)
Number of web pages : 5 : Home, About us, Products, Our Services, Contact

See here below attached Logo file.

Here some link of websites which can be taken as benchmark or source of inspiration
- https://quorbelix.com
- https://www.dralvimo.com/

Target Market(s)

Manufacturers of Functional Foods and Food Supplements in Switzerland and Europe (B2B)

Industry/Entity Type

B2B Trading of Natural & Health Ingredients

Coding

Number of Pages Required

Font styles to use
Sans Serif

Colors
0054AA
0677BA
7BADD7
CADEEF
E8F1F8
0094D4
00A9DD
6FCCEA
C7EBF8
E9F6FB
00AB8E
00BBA5
67D7C9
C6EFE9
E9F9F6
59FF00
82FF00
B8FF75
E3FFCB
F4FFEA
FFF300
FFF600
FEFA6F
FFFEC7
FFFEE8
FFC000
F8CF3A
FAE287
FDF2CF
FEFAEE
F0912C
F2A743
F7CA91
FBE8D2
FDF5EE
EE7325
F08F49
F5BC92
FAE3D3
FDF4ED

Requirements
Must have
• inspiration towards nature, sustainability, vegan food, functional food & beverages, food supplements, nutritional health, low carbon footprint
Should not have
• animals, chemistry, food additives

```html
<!DOCTYPE html>
<html lang="en">
<head>
<meta charset="utf-8">
<title>Veltrana Swiss AG – Natural &amp; Health Food Ingredients</title>
<link rel="stylesheet" href="https://fonts.googleapis.com/css2?family=Poppins:wght@600;700;800&family=IBM+Plex+Sans:wght@400;500;600;700&display=swap">
<style>
:root{
  --blue:#0054AA;
  --blue-mid:#0677BA;
  --teal:#00BBA5;
  --teal-dark:#00AB8E;
  --teal-light:#67D7C9;
  --ink:#1f2a36;
  --grey:#6b6f75;
  --line:#e3e6ea;
  --footer:#222124;
  --white:#ffffff;
}
*{box-sizing:border-box;margin:0;padding:0}
html,body{width:1200px;height:3752px;overflow:hidden}
body{position:relative;background:var(--white);font-family:"IBM Plex Sans",Arial,sans-serif;color:var(--ink)}
.abs{position:absolute}
.btn{position:absolute;display:flex;align-items:center;justify-content:center;background:var(--teal);color:var(--white);font-weight:700;border-radius:30px;text-transform:uppercase;letter-spacing:.3px}

/* hero */
.hero-photo{left:0;top:0;width:1200px;height:700px;
  clip-path:polygon(0 0,1200px 0,1200px 641px,0 692px);
  background:linear-gradient(180deg,#6f9fd6 0%,#a9c6e6 16%,#8aa3b8 30%,#4f7d5a 48%,#3f6b3a 62%,#7aa0a8 76%,#5b90b0 100%)}
.hero-accent{left:0;top:0;width:1200px;height:700px}
.site-header{left:0;top:0;width:1200px;height:100px}
.brand{position:absolute;left:143px;top:32px;font-family:"Poppins",sans-serif;font-weight:800;font-size:32px;color:var(--blue);letter-spacing:-.5px}
.main-nav{position:absolute;left:580px;top:44px;display:flex;gap:27px;font-size:14px;font-weight:600;color:#1b2430;text-transform:uppercase}
.main-nav span.active{border-bottom:3px solid var(--teal);padding-bottom:5px}
.lang{position:absolute;left:1006px;top:45px;display:flex;align-items:center;gap:10px}
.hero-title{left:0;top:168px;width:1200px;text-align:center;font-family:"Poppins",sans-serif;font-weight:800;font-size:50px;line-height:54px;color:var(--white);text-transform:uppercase;text-shadow:0 3px 6px rgba(0,0,0,.35)}
.hero-cta{left:510px;top:301px;width:180px;height:56px;font-size:17px}
.slider-dots{left:1122px;top:318px;display:flex;flex-direction:column;gap:17px}
.slider-dots i{display:block;width:13px;height:13px;border-radius:50%;background:var(--white)}
.slider-dots i.on{background:var(--teal)}

/* about */
.about-title{left:143px;top:718px;width:340px;font-family:"Poppins",sans-serif;font-weight:800;font-size:46px;line-height:54px;text-transform:uppercase;color:var(--blue)}
.about-title span{color:var(--teal)}
.about-text{left:517px;top:720px;width:540px;font-size:15.5px;line-height:29.6px;color:#4a4f55;text-align:justify}
.about-cta{left:517px;top:923px;width:162px;height:52px;font-size:15px}
.gallery-tile{top:1030px;width:295px;height:326px;border-radius:14px}
.tile-1{left:143px;background:linear-gradient(150deg,#7d6a8c,#c4583b 45%,#7aa344 75%,#d9d3c8)}
.tile-2{left:452px;background:linear-gradient(140deg,#6b4a30,#d9623a 35%,#f0b43a 60%,#8fa24a 85%,#5a3b26)}
.tile-3{left:761px;background:radial-gradient(circle at 50% 55%,#8ccf7a 0%,#2f6b35 35%,#12311d 75%),#1a3a22}
.arrow{position:absolute;top:1171px;width:44px;height:44px;border-radius:50%;border:2px solid #9aa0a6;background:var(--white);display:flex;align-items:center;justify-content:center}

/* values */
.values-photo{left:0;top:0;width:1200px;height:3752px;
  clip-path:polygon(0 1583px,495px 1497px,1200px 1380px,1200px 2645px,0 2735px);
  background:linear-gradient(180deg,#00bba5 0%,#00bba5 42%,#06a595 52%,#1b8e6b 62%,#1e9a84 72%,#2a8e86 82%,#5aa9a0 100%)}
.values-title{left:0;top:1600px;width:1200px;text-align:center;font-family:"Poppins",sans-serif;font-weight:800;font-size:46px;color:var(--white)}
.value{position:absolute;width:480px;height:160px}
.value svg{position:absolute;left:0;top:0}
.value h3{position:absolute;left:167px;top:28px;width:265px;font-family:"IBM Plex Sans",sans-serif;font-weight:700;font-size:17.5px;line-height:22px;color:var(--white);text-transform:uppercase}
.value p{margin-top:8px;font-weight:400;font-size:13.5px;line-height:21.5px;text-transform:none;color:#eafaf7;width:260px}

/* blogs */
.blog-backdrop{left:0;top:3200px;width:1200px;height:360px;background:linear-gradient(180deg,rgba(255,255,255,1) 0%,#dfe7ee 55%,#b9c6d2 100%)}
.blogs-title{left:0;top:2738px;width:1200px;text-align:center;font-family:"Poppins",sans-serif;font-weight:800;font-size:46px;color:var(--blue)}
.blogs-title span{color:var(--teal)}
.blog-grid{left:143px;top:2844px;width:913px;height:490px;display:grid;grid-template-columns:repeat(3,1fr);grid-template-rows:repeat(2,1fr);border:1px solid var(--line);background:var(--white)}
.blog-photo{width:100%;height:100%}
.photo-salad{background:radial-gradient(circle at 50% 55%,#5f8a3a 0%,#3b5a2a 35%,#2b2b2b 62%,#6b4a35 100%)}
.photo-friends{background:linear-gradient(160deg,#d9c7a0,#b9864f 40%,#7a5634 70%,#d6a45a)}
.photo-burger{background:radial-gradient(circle at 50% 55%,#6a4630 0%,#3a2a22 40%,#43552e 70%,#c9c2b6 100%)}
.blog-card{border-left:1px solid var(--line);border-right:1px solid var(--line);display:flex;flex-direction:column;align-items:center;padding-top:30px;text-align:center;background:var(--white)}
.blog-card h4{font-size:18.5px;font-weight:500;color:#222;text-transform:uppercase}
.blog-date{margin-top:8px;font-size:13px;color:var(--blue-mid);display:flex;align-items:center;gap:4px}
.blog-card p{margin-top:14px;width:245px;font-size:14px;line-height:22px;color:#8a8e93}
.blog-card .btn{position:static;margin-top:16px;width:128px;height:34px;font-size:13px}

/* footer */
.footer-shape{left:0;top:0;width:1200px;height:3752px}
.socials{left:491px;top:3543px;display:flex;gap:9px}
.socials i{display:block;width:48px;height:48px;border-radius:50%;border:2px solid var(--white)}
.footer-nav{left:0;top:3621px;width:1200px;display:flex;justify-content:center;gap:29px;font-size:19px;font-weight:700;color:var(--white)}
.copyright{left:0;top:3675px;width:1200px;text-align:center;font-size:13px;color:#e6e6e6}
</style>
</head>
<body>

<!-- hero -->
<div class="abs hero-photo" role="img" aria-label="Swiss lakeside village with church and snowy mountains"></div>
<svg class="abs hero-accent" width="1200" height="700" viewBox="0 0 1200 700" aria-hidden="true">
  <polygon points="840,656 1200,539 1200,641" fill="#0054AA"/>
</svg>

<header class="abs site-header">
  <div class="brand">Veltrana Swiss</div>
  <nav class="main-nav">
    <span class="active">Home</span><span>About</span><span>Values</span><span>Services</span><span>Contact</span>
  </nav>
  <div class="lang">
    <svg width="24" height="14" viewBox="0 0 24 14" aria-label="English"><rect width="24" height="14" fill="#1d3c8f"/><path d="M0 0L24 14M24 0L0 14" stroke="#fff" stroke-width="3"/><path d="M0 0L24 14M24 0L0 14" stroke="#c8102e" stroke-width="1"/><path d="M12 0V14M0 7H24" stroke="#fff" stroke-width="4"/><path d="M12 0V14M0 7H24" stroke="#c8102e" stroke-width="2"/></svg>
    <svg width="12" height="8" viewBox="0 0 12 8"><polygon points="0,0 12,0 6,7" fill="#1b2430"/></svg>
  </div>
</header>

<h1 class="abs hero-title">Trading natural &amp; health<br>food ingredients</h1>
<div class="btn hero-cta">Get started</div>
<div class="abs slider-dots"><i></i><i></i><i class="on"></i><i></i></div>

<!-- about -->
<h2 class="abs about-title">About<br><span>Veltrana<br>Swiss</span></h2>
<p class="abs about-text">Lorem ipsum dolor sit amet, consectetur adipiscing elit, sed do eiusmod tempor incididunt ut labore et dolore magna is ipsum suspendisse ultrices gravida. Risus commodo viverra maecenas accumsan lacus vel facilisis. Lorem ipsum dolor sit amet, consectetur adipiscing elit, sed do eiusmod tempor incididunt ut labore et dolore magna is ipsum suspendisse ultrices gravisus commodo viverra maecenas accumsan lacus vel facilisis.</p>
<div class="btn about-cta">Read more</div>

<div class="arrow" style="left:60px"><svg width="14" height="20" viewBox="0 0 14 20"><path d="M10 3L3 10L10 17" fill="none" stroke="#444" stroke-width="2.2"/></svg></div>
<div class="abs gallery-tile tile-1" role="img" aria-label="Hands holding a heart-shaped bowl of fresh fruit and vegetables"></div>
<div class="abs gallery-tile tile-2" role="img" aria-label="Fresh juices, citrus fruits and berries on a wooden table"></div>
<div class="abs gallery-tile tile-3" role="img" aria-label="Low carbon footprint concept with glass sphere and green plant"></div>
<div class="arrow" style="left:1095px"><svg width="14" height="20" viewBox="0 0 14 20"><path d="M4 3L11 10L4 17" fill="none" stroke="#444" stroke-width="2.2"/></svg></div>

<!-- values -->
<div class="abs values-photo" role="img" aria-label="Green mountain lake reflection under a teal overlay"></div>
<svg class="abs" style="left:0;top:0" width="1200" height="2760" viewBox="0 0 1200 2760" aria-hidden="true">
  <polygon points="0,1452 495,1497 0,1583" fill="#0054AA"/>
  <polygon points="720,2687 1200,2530 1200,2645" fill="#0054AA"/>
</svg>
<h2 class="abs values-title">THE VALUES</h2>

<svg width="0" height="0" style="position:absolute">
  <defs>
    <g id="hex">
      <polygon points="69,3 135,41 135,119 69,157 3,119 3,41" fill="none" stroke="rgba(255,255,255,.75)" stroke-width="2"/>
      <polygon points="69,12 127,46 127,114 69,148 11,114 11,46" fill="#fff"/>
    </g>
  </defs>
</svg>

<div class="value" style="left:146px;top:1737px">
  <svg width="138" height="160" viewBox="0 0 138 160"><use href="#hex"/>
    <g fill="none" stroke="#0054AA" stroke-width="2.5" stroke-linecap="round" stroke-linejoin="round">
      <path d="M40 90H98L92 104H46Z"/><path d="M50 90C46 76 52 62 64 58C62 70 66 80 60 90"/><path d="M74 90V64C80 60 88 62 88 72V90"/><path d="M64 58C70 50 80 52 82 58"/>
    </g></svg>
  <h3>Sourcing of natural and health ingredients<p>Lorem ipsum dolor sit amet, consectetur adipiscing elit, sed do eiusmod tempor incididunt ut labore et dolore magna</p></h3>
</div>
<div class="value" style="left:640px;top:1737px">
  <svg width="138" height="160" viewBox="0 0 138 160"><use href="#hex"/>
    <g fill="none" stroke="#0054AA" stroke-width="2.5" stroke-linecap="round" stroke-linejoin="round">
      <path d="M69 104L46 82C36 70 48 54 60 62L69 70L78 62C90 54 102 70 92 82Z"/><path d="M48 78H60L64 70L70 86L74 78H90"/>
      <circle cx="96" cy="56" r="9"/><path d="M96 51V61M91 56H101"/>
    </g></svg>
  <h3>Health &amp; nutritional health<p>Lorem ipsum dolor sit amet, consectetur adipiscing elit, sed do eiusmod tempor incididunt ut labore et dolore magna</p></h3>
</div>
<div class="value" style="left:146px;top:1937px">
  <svg width="138" height="160" viewBox="0 0 138 160"><use href="#hex"/>
    <g fill="none" stroke="#0054AA" stroke-width="2.5" stroke-linecap="round" stroke-linejoin="round">
      <path d="M64 104C44 100 40 80 50 66C58 78 66 86 64 104Z"/><path d="M74 104C94 100 98 80 88 66C80 78 72 86 74 104Z"/>
      <path d="M58 56C62 46 76 46 80 56"/><path d="M69 60C64 54 62 50 69 44C76 50 74 54 69 60Z"/>
    </g></svg>
  <h3>Eco-friendly and sustainability<p>Lorem ipsum dolor sit amet, consectetur adipiscing elit, sed do eiusmod tempor incididunt ut labore et dolore magna</p></h3>
</div>
<div class="value" style="left:640px;top:1937px">
  <svg width="138" height="160" viewBox="0 0 138 160"><use href="#hex"/>
    <g fill="none" stroke="#0054AA" stroke-width="2.5" stroke-linecap="round" stroke-linejoin="round">
      <circle cx="69" cy="70" r="22"/><circle cx="69" cy="70" r="15"/>
      <path d="M69 61L72 67L78 68L73 72L75 78L69 75L63 78L65 72L60 68L66 67Z"/>
      <path d="M56 88L48 108L58 104L62 112L68 94M82 88L90 108L80 104L76 112L70 94"/>
    </g></svg>
  <h3>High quality standard in term of products and logistic services<p>Lorem ipsum dolor sit amet, consectetur adipiscing elit, sed do eiusmod</p></h3>
</div>
<div class="value" style="left:146px;top:2136px">
  <svg width="138" height="160" viewBox="0 0 138 160"><use href="#hex"/>
    <g fill="none" stroke="#0054AA" stroke-width="2.5" stroke-linecap="round" stroke-linejoin="round">
      <path d="M69 46L86 52V66C86 76 78 82 69 86C60 82 52 76 52 66V52Z"/><path d="M61 66L67 72L78 60"/>
      <path d="M40 96H50L62 100H76C80 100 80 106 76 106H64M62 106H82L98 94C102 92 104 96 100 100L84 112H50"/><rect x="34" y="92" width="8" height="22"/>
    </g></svg>
  <h3>Trust and reliability<p>Lorem ipsum dolor sit amet, consectetur adipiscing elit, sed do eiusmod tempor incididunt ut labore et dolore magna aliquauis ipsum suspendisse</p></h3>
</div>
<div class="value" style="left:640px;top:2136px">
  <svg width="138" height="160" viewBox="0 0 138 160"><use href="#hex"/>
    <g fill="none" stroke="#0054AA" stroke-width="2.5" stroke-linecap="round" stroke-linejoin="round">
      <path d="M56 60L68 48L76 56C80 52 86 56 82 62L88 68L76 80L70 74C66 78 60 74 64 70Z"/>
      <path d="M44 86H64V94C68 90 74 94 70 100H82V112H44Z"/><path d="M86 86H100V112H86"/>
    </g></svg>
  <h3>Flexibility &amp; speed<br>to market<p>Lorem ipsum dolor sit amet, consectetur adipiscing elit, sed do eiusmod tempor incididunt ut labore et dolore magna</p></h3>
</div>
<div class="value" style="left:146px;top:2336px">
  <svg width="138" height="160" viewBox="0 0 138 160"><use href="#hex"/>
    <g fill="none" stroke="#0054AA" stroke-width="2.5" stroke-linecap="round" stroke-linejoin="round">
      <path d="M60 80C54 74 54 60 69 56C84 60 84 74 78 80V88H60Z"/><path d="M62 94H76M64 100H74"/>
      <path d="M69 48V42M52 52L48 48M86 52L90 48"/>
      <path d="M40 78V100L54 112M98 78V100L84 112"/>
    </g></svg>
  <h3>Technical advice for the development of new products<p>Lorem ipsum dolor sit amet, consectetur adipiscing elit, sed do eiusmod</p></h3>
</div>
<div class="value" style="left:640px;top:2336px">
  <svg width="138" height="160" viewBox="0 0 138 160"><use href="#hex"/>
    <g fill="none" stroke="#0054AA" stroke-width="2.5" stroke-linecap="round" stroke-linejoin="round">
      <circle cx="69" cy="80" r="32"/><rect x="55" y="76" width="28" height="24" rx="3"/>
      <path d="M60 76V68C60 56 78 56 78 68V76"/><circle cx="69" cy="86" r="3"/><path d="M69 89V94"/>
    </g></svg>
  <h3>Security of supply<p>Lorem ipsum dolor sit amet, consectetur adipiscing elit, sed do eiusmod tempor incididunt ut labore et dolore magna aliquauis ipsum suspendisse</p></h3>
</div>

<!-- blogs -->
<div class="abs blog-backdrop" role="img" aria-label="Faded alpine mountain landscape"></div>
<h2 class="abs blogs-title">LATEST <span>BLOGS</span></h2>
<div class="abs blog-grid">
  <div class="blog-photo photo-salad" role="img" aria-label="Green salad with fruit on a dark plate"></div>
  <article class="blog-card">
    <h4>At vero eos eaccusamu</h4>
    <div class="blog-date"><svg width="12" height="12" viewBox="0 0 12 12"><rect x="1" y="2" width="10" height="9" fill="none" stroke="#0677BA" stroke-width="1.3"/><path d="M1 5H11M4 1V3M8 1V3" stroke="#0677BA" stroke-width="1.3"/></svg>April 25,2022</div>
    <p>At vero eos et accusamus et iusto odio dignissiducimumos ducimus qui blanditiis pducimuducimuraesentiu</p>
    <div class="btn">Read more</div>
  </article>
  <div class="blog-photo photo-friends" role="img" aria-label="Friends sharing a meal and drinks outdoors"></div>
  <article class="blog-card">
    <h4>At vero eos eaccusamu</h4>
    <div class="blog-date"><svg width="12" height="12" viewBox="0 0 12 12"><rect x="1" y="2" width="10" height="9" fill="none" stroke="#0677BA" stroke-width="1.3"/><path d="M1 5H11M4 1V3M8 1V3" stroke="#0677BA" stroke-width="1.3"/></svg>April 25,2022</div>
    <p>At vero eos et accusamus et iusto odio dignissiducimumos ducimus qui blanditiis pducimuducimuraesentiu</p>
    <div class="btn">Read more</div>
  </article>
  <div class="blog-photo photo-burger" role="img" aria-label="Plant-based burgers and patties with spinach"></div>
  <article class="blog-card">
    <h4>At vero eos eaccusamu</h4>
    <div class="blog-date"><svg width="12" height="12" viewBox="0 0 12 12"><rect x="1" y="2" width="10" height="9" fill="none" stroke="#0677BA" stroke-width="1.3"/><path d="M1 5H11M4 1V3M8 1V3" stroke="#0677BA" stroke-width="1.3"/></svg>April 25,2022</div>
    <p>At vero eos et accusamus et iusto odio dignissiducimumos ducimus qui blanditiis pducimuducimuraesentiu</p>
    <div class="btn">Read more</div>
  </article>
</div>

<!-- footer -->
<svg class="abs footer-shape" width="1200" height="3752" viewBox="0 0 1200 3752" aria-hidden="true">
  <polygon points="0,3553 1200,3435 1200,3752 0,3752" fill="#222124"/>
  <polygon points="0,3450 615,3493 0,3553" fill="#0054AA"/>
</svg>
<div class="abs socials"><i></i><i></i><i></i><i></i></div>
<nav class="abs footer-nav">
  <span>HOME</span><span>/</span><span>ABOUT</span><span>/</span><span>VALUES</span><span>/</span><span>SERVICES</span><span>/</span><span>CONTACT</span>
</nav>
<p class="abs copyright">© 2022 Veltrana Swiss AG. All rights reserved &nbsp;|&nbsp; Privacy &nbsp;|&nbsp; Terms of Use</p>

</body>
</html>
```